Fernhollow Architectural Systems Business Card

We have a logo - but we need a business card. We are a specialty manufacturer of wood wall and ceiling panels. Please visit our website - www.fernhollowpanels.com to see examples of our products.
We create wood architectural systems - so we would love to see wood on the card somehow. Maybe something similar to our grille system?
We would like a spot on the business card for a QR code that people can scan to add the contact to their phone (we have the QR codes - just need a spot on the card).
As for the contact info - we want to keep it simple. (Name, Cell phone, Fax, email, website)

Target Market(s)

Architects and general contractors

Industry/Entity Type

Construction

Contact Information for Business Card

Name, Cell phone, fax, email, website

Requirements
Must have
• space for a QR code, wood feature
Nice to have
• We just want something a little different - but not too crazy. We want to stand out - but in a professional way.
Should not have
• nothing too busy

```html
<!DOCTYPE html>
<html lang="en">
<head>
<meta charset="utf-8">
<title>Fernhollow Architectural Systems – Business Card</title>
<link rel="stylesheet" href="https://fonts.googleapis.com/css2?family=Open+Sans:wght@400;700;800&display=swap">
<style>
  :root {
    --backdrop: #2d2b2c;
    --brand-red: #b30000;
    --ink: #1e1e1e;
    --paper: #ffffff;
    --wood-light: #eccb9c;
    --wood-mid: #e2b67f;
    --wood-deep: #d9a66a;
    --stroke: #0b0b0b;
  }
  * { margin: 0; padding: 0; box-sizing: border-box; }
  html, body {
    width: 887px; height: 1200px; overflow: hidden;
    background: var(--backdrop);
    font-family: "Open Sans", Arial, sans-serif;
  }
  .canvas { position: relative; width: 887px; height: 1200px; }

  .card {
    position: absolute; left: 0; width: 887px;
    border-radius: 38px; overflow: hidden;
  }
  .card--front { top: 8px; height: 573px; }
  .card--back { top: 619px; height: 574px; background: var(--paper); }

  .wood-panel {
    position: absolute; inset: 0;
    background:
      repeating-linear-gradient(90deg, rgba(150,95,40,0.10) 0 1px, transparent 1px 55px),
      linear-gradient(90deg, var(--wood-light), var(--wood-mid) 40%, var(--wood-light) 70%, var(--wood-deep));
  }
  .wave { position: absolute; inset: 0; width: 887px; height: 573px; }

  .wordmark {
    position: absolute; display: flex; align-items: center;
    color: var(--brand-red); font-weight: 800;
  }
  .wordmark__dot { border-radius: 50%; background: var(--brand-red); flex: none; }
  .wordmark__text { display: flex; flex-direction: column; line-height: 1; }
  .wordmark__name { letter-spacing: 0.02em; }
  .wordmark__sub { letter-spacing: 0.24em; }

  .wordmark--front { left: 59px; top: 128px; gap: 26px; }
  .wordmark--front .wordmark__dot { width: 140px; height: 140px; }
  .wordmark--front .wordmark__name { font-size: 58px; }
  .wordmark--front .wordmark__sub { font-size: 19px; margin-top: 12px; }

  .wordmark--back { left: 493px; top: 683px; gap: 14px; }
  .wordmark--back .wordmark__dot { width: 84px; height: 84px; }
  .wordmark--back .wordmark__name { font-size: 33px; }
  .wordmark--back .wordmark__sub { font-size: 10.5px; margin-top: 8px; }

  .qr-spot {
    position: absolute; left: 698px; top: 400px;
    width: 120px; height: 120px;
    border: 1.5px solid var(--paper);
  }

  .person-name {
    position: absolute; left: 73px; top: 236px;
    font-size: 40px; color: var(--brand-red); font-weight: 400; letter-spacing: 0.01em;
  }
  .person-name strong { font-weight: 700; }

  .contact-list { position: absolute; left: 71px; top: 325px; list-style: none; }
  .contact-list li {
    display: flex; align-items: center; height: 52px;
    font-size: 19px; color: var(--ink); letter-spacing: 0.02em;
  }
  .contact-list svg { width: 33px; height: 33px; margin-right: 11px; fill: var(--brand-red); flex: none; }
</style>
</head>
<body>
<div class="canvas">

  <section class="card card--front">
    <div class="wood-panel" role="img" aria-label="Light pine wood plank wall texture"></div>
    <svg class="wave" viewBox="0 0 887 573" aria-hidden="true">
      <path d="M0 487 C70 510 140 522 182 518 C380 515 520 420 590 382 C680 333 740 332 787 336 C830 340 860 352 887 366 L887 573 L0 573 Z" fill="var(--brand-red)"/>
      <path d="M0 487 C70 510 140 522 182 518 C380 515 520 420 590 382 C680 333 740 332 787 336 C830 340 860 352 887 366" fill="none" stroke="var(--stroke)" stroke-width="3"/>
    </svg>
    <div class="wordmark wordmark--front">
      <span class="wordmark__dot"></span>
      <span class="wordmark__text">
        <span class="wordmark__name">FERNHOLLOW</span>
        <span class="wordmark__sub">ARCHITECTURAL SYSTEMS</span>
      </span>
    </div>
    <div class="qr-spot" aria-label="Space for QR code"></div>
  </section>

  <section class="card card--back">
    <div class="wordmark wordmark--back" style="top:64px;">
      <span class="wordmark__dot"></span>
      <span class="wordmark__text">
        <span class="wordmark__name">FERNHOLLOW</span>
        <span class="wordmark__sub">ARCHITECTURAL SYSTEMS</span>
      </span>
    </div>

    <h1 class="person-name"><strong>NAME</strong> HERE</h1>

    <ul class="contact-list">
      <li>
        <svg viewBox="0 0 24 24" aria-hidden="true"><path d="M6.6 2.5c.6-.3 1.3-.1 1.6.5l1.9 3.4c.3.6.2 1.2-.3 1.6L8.3 9.3c.9 2.3 3.9 5.6 6.4 6.6l1.3-1.4c.4-.5 1.1-.6 1.6-.3l3.4 1.9c.6.3.8 1 .5 1.6l-1 2.2c-.4.9-1.4 1.4-2.4 1.2C10.3 19.8 4.2 13.7 2.8 6c-.2-1 .3-2 1.2-2.4z"/></svg>
        +0123-456-789
      </li>
      <li>
        <svg viewBox="0 0 24 24" aria-hidden="true"><path d="M7 2h9v5H7z"/><path d="M3 8h18v9h-3v5H6v-5H3zm5 8v4h8v-4zm1 1h6v.8H9zm0 1.6h6v.8H9z" fill-rule="evenodd"/></svg>
        +0123-456-789
      </li>
      <li>
        <svg viewBox="0 0 24 24" aria-hidden="true"><path d="M12 2a10 10 0 1 0 5 18.7l-.9-1.6A8.2 8.2 0 1 1 20.2 12c0 1.6-.8 2.9-1.9 2.9-.9 0-1.3-.6-1.3-1.6V7.5h-1.8v.9a4.3 4.3 0 1 0 .3 6.1c.5 1.3 1.6 2.2 2.9 2.2 2.2 0 3.6-2.1 3.6-4.7A10 10 0 0 0 12 2zm0 12.6a2.6 2.6 0 1 1 0-5.2 2.6 2.6 0 0 1 0 5.2z"/></svg>
        emailaddress@fernhollowmail.com
      </li>
      <li>
        <svg viewBox="0 0 24 24" aria-hidden="true"><path d="M12 2a10 10 0 1 0 0 20 10 10 0 0 0 0-20zm-1 2.1V7H8.3c.7-1.5 1.6-2.6 2.7-2.9zm2 0c1.1.3 2 1.4 2.7 2.9H13zM6.2 7H4.9a8 8 0 0 1 3-2.3c-.6.6-1.2 1.4-1.7 2.3zm11.6 0c-.5-.9-1.1-1.7-1.7-2.3a8 8 0 0 1 3 2.3zM4.1 11a8 8 0 0 1 .6-2.3h2.8c-.2.7-.3 1.5-.3 2.3zm5 0c0-.8.1-1.6.3-2.3H11V11zm3.9 0V8.7h3.6c.2.7.3 1.5.3 2.3zm5.9 0c0-.8-.1-1.6-.3-2.3h2.8c.3.7.5 1.5.6 2.3zM4.1 13h3.1c0 .8.1 1.6.3 2.3H4.7A8 8 0 0 1 4.1 13zm5 0H11v2.3H9.4c-.2-.7-.3-1.5-.3-2.3zm3.9 0h3.9c0 .8-.1 1.6-.3 2.3H13zm5.9 0h3.1a8 8 0 0 1-.6 2.3h-2.8c.2-.7.3-1.5.3-2.3zM4.9 17h1.3c.5.9 1.1 1.7 1.7 2.3a8 8 0 0 1-3-2.3zm3.4 0H11v2.9c-1.1-.3-2-1.4-2.7-2.9zm4.7 0h2.7c-.7 1.5-1.6 2.6-2.7 2.9zm4.8 0h1.3a8 8 0 0 1-3 2.3c.6-.6 1.2-1.4 1.7-2.3z"/></svg>
        www.fernhollowpanels.com
      </li>
    </ul>
  </section>

</div>
</body>
</html>
```